Oil Field Service company needs professional business cards

Looking to clean up our current company business cards and look a little more professional. Brenwick Casing Services is a US based company that services the oil field. We deal with engineers, managers and oil rigs....................................................................................................................................................................................................................................................................................................................................................................................................

Target Market(s)

Oil and Gas professionals

Industry/Entity Type

Oil And Gas

Contact Information for Business Card

See attached photo as example

Font styles to use
Sans Serif

Colors
ec1f27

Requirements
Must have
• Company Logo, Name, Title, Cell, Office, Fax, Email.
• See attached photo
Nice to have
• External CRT, Internal CRT, Casing Crews, Torque Turn, Laydown Machine
Should not have
• Do not introduce any new pictures and keep it professional looking

```html
<!DOCTYPE html>
<html lang="en">
<head>
<meta charset="utf-8">
<title>Brenwick Casing Services – Business Card</title>
<link rel="stylesheet" href="https://fonts.googleapis.com/css2?family=Archivo:wght@400;600;700;800&family=Oswald:wght@400;500&family=Roboto:wght@400&display=swap">
<style>
  :root {
    --brand-red: #d4231f;
    --slate: #3c4f61;
    --ink: #2d2d2d;
    --muted: #555a60;
    --card: #f7f7f7;
    --backdrop: #e4e4e4;
  }
  * { box-sizing: border-box; margin: 0; padding: 0; }
  html, body { width: 1200px; height: 576px; overflow: hidden; }
  body { background: var(--backdrop); position: relative; font-family: "Archivo", Arial, sans-serif; }

  .card {
    position: absolute;
    background: var(--card);
    border-radius: 6px;
    box-shadow: 0 2px 5px rgba(0,0,0,0.25);
    overflow: hidden;
  }

  /* Front */
  .card--front { left: 81px; top: 139px; width: 485px; height: 293px; }
  .front__name {
    position: absolute; left: 0; right: 0; top: 82px;
    text-align: center;
    font-weight: 800; font-size: 34px; letter-spacing: 1px;
    text-transform: uppercase; color: var(--slate);
    line-height: 1.15;
  }
  .front__services {
    position: absolute; left: 0; right: 0; top: 221px; height: 26px;
    background: var(--brand-red);
    display: flex; align-items: center; justify-content: center; gap: 8px;
    color: #fff; font-weight: 600; font-size: 12.5px; letter-spacing: 0.2px;
  }
  .front__services .sep { opacity: 0.9; }
  .front__web {
    position: absolute; left: 0; right: 0; top: 261px;
    display: flex; align-items: center; justify-content: center; gap: 10px;
    font-size: 13px; color: var(--ink);
  }
  .front__web .rule { width: 66px; height: 2px; background: var(--brand-red); border-radius: 1px; }

  /* Back */
  .card--back { left: 602px; top: 138px; width: 481px; height: 292px; }
  .back__name {
    position: absolute; left: 20px; width: 210px; top: 62px;
    text-align: center;
    font-weight: 800; font-size: 19px; letter-spacing: 0.5px;
    text-transform: uppercase; color: var(--slate); line-height: 1.2;
  }
  .back__services {
    position: absolute; left: 20px; width: 210px; top: 156px;
    list-style: none; text-align: center;
    font-weight: 600; font-size: 13.5px; line-height: 18px; color: var(--ink);
  }
  .back__divider {
    position: absolute; left: 243px; top: 42px; width: 1px; height: 208px;
    background: var(--brand-red);
  }
  .person { position: absolute; left: 270px; top: 64px; }
  .person__name { font-family: "Oswald", Arial, sans-serif; font-weight: 400; font-size: 22px; color: var(--brand-red); line-height: 1.1; }
  .person__title { font-family: "Roboto", Arial, sans-serif; font-size: 11.5px; color: var(--muted); margin-top: 3px; }

  .contacts { position: absolute; left: 272px; top: 143px; list-style: none; }
  .contacts li {
    display: flex; align-items: center; gap: 9px; height: 16px;
    font-family: "Oswald", Arial, sans-serif; font-size: 11.5px; color: var(--ink);
  }
  .contacts svg { width: 10px; height: 10px; fill: var(--brand-red); flex: none; }
</style>
</head>
<body>

  <section class="card card--front" aria-label="Card front">
    <div class="front__name">Brenwick Casing Services</div>
    <div class="front__services">
      <span>LAYDOWN MACHINE</span><span class="sep">|</span>
      <span>CASING CREW</span><span class="sep">|</span>
      <span>MUD TOOL</span><span class="sep">|</span>
      <span>TORQUE TURN</span>
    </div>
    <div class="front__web"><span class="rule"></span><span>www.brenwickcs.com</span><span class="rule"></span></div>
  </section>

  <section class="card card--back" aria-label="Card back">
    <div class="back__name">Brenwick<br>Casing Services</div>
    <ul class="back__services">
      <li>Laydown Machine</li>
      <li>Casing Crew</li>
      <li>Mud Tool</li>
      <li>Torque Turn</li>
    </ul>
    <div class="back__divider"></div>

    <div class="person">
      <div class="person__name">Cody Harlan</div>
      <div class="person__title">Area Manager</div>
    </div>

    <ul class="contacts">
      <li><svg viewBox="0 0 10 10" aria-hidden="true"><path d="M2 0.5l1.6 2-0.9 1a6 6 0 0 0 3.8 3.8l1-0.9 2 1.6-1 1.5C4.5 9.5 0.5 5.5 0.5 1.5z"/></svg>(555) 214-3800</li>
      <li><svg viewBox="0 0 10 10" aria-hidden="true"><path d="M0.5 3.5C2 1.5 8 1.5 9.5 3.5L8.5 5 7 4.3V3.5H3v0.8L1.5 5z M2 6h6v3H2z"/></svg>(555) 309-6142</li>
      <li><svg viewBox="0 0 10 10" aria-hidden="true"><path d="M2.5 0.5h5v2.5h-5z M0.5 3.5h9v4h-2V9h-5V7.5h-2z"/></svg>(555) 214-3815</li>
      <li><svg viewBox="0 0 10 10" aria-hidden="true"><path d="M5 0.3a3.4 3.4 0 0 1 3.4 3.4C8.4 6.2 5 9.8 5 9.8S1.6 6.2 1.6 3.7A3.4 3.4 0 0 1 5 0.3zm0 2a1.4 1.4 0 1 0 0 2.8 1.4 1.4 0 0 0 0-2.8z"/></svg>Fairbend, OK 73055</li>
      <li><svg viewBox="0 0 10 10" aria-hidden="true"><path d="M0.5 2h9v6h-9z" fill="none" stroke="#d4231f" stroke-width="1"/><path d="M0.5 2L5 5.5 9.5 2" fill="none" stroke="#d4231f" stroke-width="1"/></svg>codyharlan@brenwickcs.com</li>
      <li><svg viewBox="0 0 10 10" aria-hidden="true"><circle cx="5" cy="5" r="4.3" fill="none" stroke="#d4231f" stroke-width="1"/><path d="M0.7 5h8.6M5 0.7c-2.2 2.4-2.2 6.2 0 8.6M5 0.7c2.2 2.4 2.2 6.2 0 8.6" fill="none" stroke="#d4231f" stroke-width="0.8"/></svg>www.brenwickcs.com</li>
    </ul>
  </section>

</body>
</html>
```